High-end construction company needs a business card design

We need a modern looking business card that draws people in, is memorable and looks so good people will want to sick it on their fridges.
On the first side what is needed are:
Logo
My name - Tomasz Brelwik
Title - Managing Director
Website - www.varkelt.co.uk
Email - tomasz@varkelt.co.uk
Telephone - 020 5194 6281
Mobile - 07845139072
On the back side was is needed is a list of all the services we provide:
-Kitchen Renovations
-Bathroom Renovations
-House Renovations
-Garage Conversions
-Extensions
-Loft Conversions
-Conservatories
-Carpentry
-Tiling
-Electrical
-Plumbing & Heating
-Bricklaying
-Landscaping
-Decorating
-Plastering
We would like the colours to be the same shades as on the logo with grey or black for the words.
Target Market(s)
Anyone who needs building work done
Contact Information for Business Card
This business card is for a construction company which strives to deliver excellent service and quality.
The look and feel of the card should represent this.
Requirements
Must have
- On the first side what is needed are:
Logo
My name - Tomasz Brelwik
Title - Managing Director
Website - www.varkelt.co.uk
Email - tomasz@varkelt.co.uk
Telephone - 020 5194 6281
Mobile - 07845139072
Nice to have
- Cool looking features

```html
<!DOCTYPE html>
<html lang="en">
<head>
<meta charset="utf-8">
<title>Varkelt Construction Ltd – Business Card</title>
<link rel="stylesheet" href="https://fonts.googleapis.com/css2?family=Montserrat:wght@500;700&family=Open+Sans:wght@400;600&display=swap">
<style>
  :root {
    --stage: #4a4a4a;
    --card: #ffffff;
    --green: #7cc242;
    --green-dark: #3d8b37;
    --green-band: #80c45a;
    --ink: #1f2326;
    --shadow: rgba(0,0,0,0.45);
  }
  * { box-sizing: border-box; margin: 0; padding: 0; }
  html, body { width: 1200px; height: 982px; overflow: hidden; }
  body { background: var(--stage); position: relative; font-family: "Open Sans", sans-serif; }

  .card {
    position: absolute; left: 303px; width: 622px; height: 357px;
    border-radius: 40px; background: var(--card); overflow: hidden;
    box-shadow: 4px 8px 18px var(--shadow);
  }
  .card--services { top: 113px; background: var(--green); }
  .card--contact { top: 513px; }

  .card-shape { position: absolute; left: 0; top: 0; }

  .brand {
    position: absolute; font-family: "Montserrat", sans-serif; font-weight: 700;
    color: var(--green); text-align: center; z-index: 2;
  }
  .brand-mark { display: block; width: 14px; height: 14px; background: var(--green); margin: 0 auto 4px; }
  .brand-name { display: block; line-height: 1; letter-spacing: 0.5px; }
  .brand-sub { display: block; letter-spacing: 2px; }

  .card--services .brand { left: 0; width: 622px; top: 72px; }
  .card--services .brand-name { font-size: 44px; }
  .card--services .brand-sub { font-size: 16px; line-height: 18px; letter-spacing: 2.5px; }

  .services {
    position: absolute; top: 210px; left: 26px; display: grid;
    grid-template-columns: 234px 178px 190px; row-gap: 6px; list-style: none;
  }
  .services li { display: flex; align-items: center; gap: 6px; color: #fff; font-size: 16px; height: 20px; white-space: nowrap; }
  .tick { width: 16px; height: 16px; flex: none; }

  .person { position: absolute; left: 46px; top: 76px; }
  .person-name { font-family: "Montserrat", sans-serif; font-weight: 500; font-size: 22px; letter-spacing: 1.5px; color: var(--ink); }
  .person-title { font-family: "Montserrat", sans-serif; font-weight: 500; font-size: 15.5px; letter-spacing: 1.3px; color: var(--green-dark); opacity: .85; margin-top: 2px; }

  .card--contact .brand { left: 374px; width: 208px; top: 92px; }
  .card--contact .brand-name { font-size: 38px; }
  .card--contact .brand-sub { font-size: 13px; line-height: 14px; }

  .divider { position: absolute; top: 153px; height: 3px; background: var(--green); }
  .divider--left { left: 0; width: 372px; }
  .divider--right { left: 584px; width: 38px; }

  .motif { position: absolute; left: 40px; top: 30px; width: 500px; height: 300px;
    background: radial-gradient(ellipse at center, rgba(124,194,66,0.07), rgba(124,194,66,0) 70%); }

  .contact { position: absolute; list-style: none; top: 266px; font-size: 15.5px; color: var(--ink); }
  .contact li { display: flex; align-items: center; gap: 8px; height: 26px; }
  .contact--phones { left: 46px; }
  .contact--web { right: 46px; text-align: right; }
  .icon { width: 14px; height: 14px; flex: none; }

  .web-band {
    position: absolute; left: 0; bottom: 0; width: 622px; height: 31px; background: var(--green-band);
    color: #fff; font-weight: 600; font-size: 15px; letter-spacing: 2px; text-align: center; line-height: 31px;
  }
</style>
</head>
<body>

<section class="card card--services" aria-label="Services side">
  <svg class="card-shape" width="622" height="357" viewBox="0 0 622 357" aria-hidden="true">
    <path d="M0 0 H622 V145 Q311 222 0 145 Z" fill="var(--card)"/>
    <path d="M34 150 Q311 222 592 150 Q311 200 34 150 Z" fill="var(--green-dark)"/>
  </svg>
  <div class="brand"><span class="brand-mark"></span><span class="brand-name">VARKELT</span><span class="brand-sub">CONSTRUCTION LTD</span></div>
  <ul class="services">
    <li><svg class="tick" viewBox="0 0 16 16"><circle cx="8" cy="8" r="6.8" fill="none" stroke="#fff" stroke-width="1.5"/><path d="M4.8 8.2 7.2 10.5 11.4 5.6" fill="none" stroke="#fff" stroke-width="1.6"/></svg>Kitchen Renovations</li>
    <li><svg class="tick" viewBox="0 0 16 16"><circle cx="8" cy="8" r="6.8" fill="none" stroke="#fff" stroke-width="1.5"/><path d="M4.8 8.2 7.2 10.5 11.4 5.6" fill="none" stroke="#fff" stroke-width="1.6"/></svg>Loft Conversions</li>
    <li><svg class="tick" viewBox="0 0 16 16"><circle cx="8" cy="8" r="6.8" fill="none" stroke="#fff" stroke-width="1.5"/><path d="M4.8 8.2 7.2 10.5 11.4 5.6" fill="none" stroke="#fff" stroke-width="1.6"/></svg>Plumbing &amp; Heating</li>
    <li><svg class="tick" viewBox="0 0 16 16"><circle cx="8" cy="8" r="6.8" fill="none" stroke="#fff" stroke-width="1.5"/><path d="M4.8 8.2 7.2 10.5 11.4 5.6" fill="none" stroke="#fff" stroke-width="1.6"/></svg>Bathroom Renovations</li>
    <li><svg class="tick" viewBox="0 0 16 16"><circle cx="8" cy="8" r="6.8" fill="none" stroke="#fff" stroke-width="1.5"/><path d="M4.8 8.2 7.2 10.5 11.4 5.6" fill="none" stroke="#fff" stroke-width="1.6"/></svg>Conservatories</li>
    <li><svg class="tick" viewBox="0 0 16 16"><circle cx="8" cy="8" r="6.8" fill="none" stroke="#fff" stroke-width="1.5"/><path d="M4.8 8.2 7.2 10.5 11.4 5.6" fill="none" stroke="#fff" stroke-width="1.6"/></svg>Bricklaying</li>
    <li><svg class="tick" viewBox="0 0 16 16"><circle cx="8" cy="8" r="6.8" fill="none" stroke="#fff" stroke-width="1.5"/><path d="M4.8 8.2 7.2 10.5 11.4 5.6" fill="none" stroke="#fff" stroke-width="1.6"/></svg>House Renovations</li>
    <li><svg class="tick" viewBox="0 0 16 16"><circle cx="8" cy="8" r="6.8" fill="none" stroke="#fff" stroke-width="1.5"/><path d="M4.8 8.2 7.2 10.5 11.4 5.6" fill="none" stroke="#fff" stroke-width="1.6"/></svg>Carpentry</li>
    <li><svg class="tick" viewBox="0 0 16 16"><circle cx="8" cy="8" r="6.8" fill="none" stroke="#fff" stroke-width="1.5"/><path d="M4.8 8.2 7.2 10.5 11.4 5.6" fill="none" stroke="#fff" stroke-width="1.6"/></svg>Landscaping</li>
    <li><svg class="tick" viewBox="0 0 16 16"><circle cx="8" cy="8" r="6.8" fill="none" stroke="#fff" stroke-width="1.5"/><path d="M4.8 8.2 7.2 10.5 11.4 5.6" fill="none" stroke="#fff" stroke-width="1.6"/></svg>Garage Conversions</li>
    <li><svg class="tick" viewBox="0 0 16 16"><circle cx="8" cy="8" r="6.8" fill="none" stroke="#fff" stroke-width="1.5"/><path d="M4.8 8.2 7.2 10.5 11.4 5.6" fill="none" stroke="#fff" stroke-width="1.6"/></svg>Tiling</li>
    <li><svg class="tick" viewBox="0 0 16 16"><circle cx="8" cy="8" r="6.8" fill="none" stroke="#fff" stroke-width="1.5"/><path d="M4.8 8.2 7.2 10.5 11.4 5.6" fill="none" stroke="#fff" stroke-width="1.6"/></svg>Decorating</li>
    <li><svg class="tick" viewBox="0 0 16 16"><circle cx="8" cy="8" r="6.8" fill="none" stroke="#fff" stroke-width="1.5"/><path d="M4.8 8.2 7.2 10.5 11.4 5.6" fill="none" stroke="#fff" stroke-width="1.6"/></svg>Extensions</li>
    <li><svg class="tick" viewBox="0 0 16 16"><circle cx="8" cy="8" r="6.8" fill="none" stroke="#fff" stroke-width="1.5"/><path d="M4.8 8.2 7.2 10.5 11.4 5.6" fill="none" stroke="#fff" stroke-width="1.6"/></svg>Electrical</li>
    <li><svg class="tick" viewBox="0 0 16 16"><circle cx="8" cy="8" r="6.8" fill="none" stroke="#fff" stroke-width="1.5"/><path d="M4.8 8.2 7.2 10.5 11.4 5.6" fill="none" stroke="#fff" stroke-width="1.6"/></svg>Plastering</li>
  </ul>
</section>

<section class="card card--contact" aria-label="Contact side">
  <div class="motif" role="img" aria-label="Faint brand motif in the card background"></div>
  <div class="person">
    <p class="person-name">TOMASZ BRELWIK</p>
    <p class="person-title">MANAGING DIRECTOR</p>
  </div>
  <div class="divider divider--left"></div>
  <div class="divider divider--right"></div>
  <div class="brand"><span class="brand-mark"></span><span class="brand-name">VARKELT</span><span class="brand-sub">CONSTRUCTION LTD</span></div>

  <ul class="contact contact--phones">
    <li><svg class="icon" viewBox="0 0 14 14"><path d="M3 1 5.2 3.6 4 5.2Q5.4 8.4 8.8 10L10.4 8.8 13 11 11.4 13Q6 12.6 1 3Z" fill="var(--green)"/></svg>020 5194 6281</li>
    <li><svg class="icon" viewBox="0 0 14 14"><rect x="3.5" y="0.8" width="7" height="12.4" rx="1.4" fill="none" stroke="var(--green)" stroke-width="1.6"/><circle cx="7" cy="10.8" r="0.9" fill="var(--green)"/></svg>07845139072</li>
  </ul>
  <ul class="contact contact--web">
    <li>tomasz@varkelt.co.uk<svg class="icon" viewBox="0 0 14 14"><rect x="0.5" y="2.5" width="13" height="9" rx="1" fill="var(--green)"/><path d="M1 3 7 7.8 13 3" fill="none" stroke="#fff" stroke-width="1.2"/></svg></li>
    <li>www.varkelt.co.uk<svg class="icon" viewBox="0 0 14 14"><circle cx="7" cy="7" r="6.2" fill="none" stroke="var(--green)" stroke-width="1.4"/><ellipse cx="7" cy="7" rx="2.6" ry="6.2" fill="none" stroke="var(--green)" stroke-width="1.2"/><path d="M1 7H13" stroke="var(--green)" stroke-width="1.2"/></svg></li>
  </ul>

  <div class="web-band">WWW.VARKELT.CO.UK</div>
</section>

</body>
</html>
```